Website redesign for job agency recruitment

Please refer to the attached document, “Tarvenly Work Website Brief,” for comprehensive details regarding the scope, objectives, and requirements of this website redesign project.

For imagery you can use images from this website https://www.pixelmarrowfoto.com or any other you regularly use.

Target Market(s)

Jobseekers and Companies looking for general labour

Industry/Entity Type

Services: Oil, Gas and Mining, Administrative, Construction and Trades, Warehouse and Logistics and, Manufacturing.

Number of Pages Required

5+ page

Font styles to use
Serif
Other font styles liked:
• Inter, Open-Sans or similar.

Requirements
Must have
• The requirements highlighted in the Word document attached. The final design needs to be provided in Figma including all viewports (Desktop, mobiel and tablet)
Should not have
• Website we like as a reference: www.brevicktalentco.com, www.qelvaworks.com, www.zunmarra.com, www.ferrowhires.com, www.9vtalentpool.com, www.hiringwithtrello.ca

```html
<!DOCTYPE html>
<html lang="en">
<head>
<meta charset="utf-8">
<title>Tarvenly Work Agency – Website Redesign</title>
<link href="https://fonts.googleapis.com/css2?family=Farro:wght@400;500;700&family=Inter:wght@400;500;600&display=swap" rel="stylesheet">
<style>
:root{
  --gold:#f2b90f;
  --blue:#0d3a8c;
  --navy:#0b2148;
  --ink:#111111;
  --board:#c9c9c9;
  --muted:#555a63;
  --soft:#f3f3f3;
}
*{margin:0;padding:0;box-sizing:border-box}
html,body{width:679px;height:1200px;overflow:hidden;background:var(--board)}
body{position:relative;font-family:"Inter",sans-serif;color:var(--ink)}
.abs{position:absolute}
.farro{font-family:"Farro",sans-serif}

/* Presentation header */
.board-head{position:absolute;left:0;top:0;width:679px;height:184px;
  background:linear-gradient(100deg,#0e1527 0%,#1b2233 45%,#4a3a22 80%,#6b4d22 100%)}
.brand-mark{left:36px;top:40px;width:70px;height:70px;border-radius:50%;border:3px solid var(--gold)}
.brand-name{left:32px;top:121px;font-family:"Farro",sans-serif;font-size:13px;color:#2f5bc4;font-weight:500}
.brand-tag{left:32px;top:140px;font-family:"Farro",sans-serif;font-size:8px;color:#dddddd}
.title{left:340px;top:26px;font-family:"Farro",sans-serif;font-weight:700;font-size:27px;line-height:31px;color:#fff}
.meta{font-family:"Farro",sans-serif;font-weight:700;font-size:16px;color:#fff}
.swatch{top:129px;width:23px;height:21px;border-radius:4px;border:1px solid #ddd}

.view-label{left:38px;top:200px;font-family:"Farro",sans-serif;font-weight:700;font-size:9.5px}

/* Website frame */
.site{position:absolute;left:38px;top:224px;width:360px;height:911px;background:#fff;overflow:hidden}
.topbar-call{left:162px;top:0;width:92px;height:15px;background:var(--blue);clip-path:polygon(5px 0,100% 0,calc(100% - 5px) 100%,0 100%);color:#fff;font-size:4.2px;display:flex;align-items:center;justify-content:center;gap:2px}
.topbar-reg{left:250px;top:0;width:110px;height:15px;background:var(--gold);clip-path:polygon(5px 0,100% 0,100% 100%,0 100%);font-size:4.2px;font-weight:600;display:flex;align-items:center;padding-left:18px;gap:5px}
.site-logo{left:52px;top:3px;display:flex;align-items:center;gap:3px}
.site-logo .dot{width:14px;height:14px;border-radius:50%;border:1.5px solid var(--gold)}
.site-logo span{font-family:"Farro",sans-serif;font-size:5px;color:var(--blue);font-weight:500;width:40px;line-height:6px}
.nav{top:25px;font-size:4.2px;font-weight:500}
.nav.active{color:var(--blue)}

.hero{left:0;top:36px;width:360px;height:192px;background:linear-gradient(180deg,#1a2d52 0%,#0d2858 60%,#0a2150 100%)}
.hero h1{left:39px;top:76px;width:160px;font-family:"Farro",sans-serif;font-weight:700;font-size:12.6px;line-height:18px;color:#fff}
.hero p{left:39px;top:135px;width:130px;font-size:5px;line-height:8.2px;color:#e8ecf5}
.btn{height:15px;font-family:"Farro",sans-serif;font-weight:500;font-size:6px;display:flex;align-items:center;padding-left:8px}
.btn-blue{background:var(--blue);color:#fff}
.btn-gold{background:var(--gold);color:var(--ink)}
.orb{left:205px;top:60px;width:131px;height:131px;border-radius:50%;border:3px solid rgba(255,255,255,.55);
  background:radial-gradient(circle at 50% 35%,#e6c08a 0%,#a57446 45%,#5a4430 100%)}
.pin{width:23px;height:23px;border-radius:50%;background:#fff;display:flex;align-items:center;justify-content:center;box-shadow:0 1px 3px rgba(0,0,0,.3)}
.pin.on{background:var(--gold)}
.service-pill{left:226px;top:139px;width:72px;height:12px;border-radius:6px;background:#fff;font-family:"Farro",sans-serif;font-size:4px;display:flex;align-items:center;padding-left:5px;gap:4px}
.service-pill i{width:8px;height:8px;border-radius:50%;background:var(--gold);display:inline-block}

.sec-title{font-family:"Farro",sans-serif;font-weight:700;font-size:9.3px}
.hl{background:var(--gold);padding:0 1.5px}
.body-txt{font-size:4.2px;line-height:6.8px;color:var(--muted)}
.photo-team{left:42px;top:249px;width:124px;height:130px;background:linear-gradient(160deg,#8fa2b5 0%,#c9b296 60%,#7d6a55 100%)}
.photo-hand{left:126px;top:326px;width:52px;height:54px;background:linear-gradient(180deg,#5b6472,#2e333c);border:1.5px solid #fff}
.photo-frame{left:52px;top:259px;width:120px;height:129px;border:.6px solid var(--gold)}

.sectors{left:0;top:399px;width:360px;height:223px;background:var(--soft)}
.sec-list{left:40px;top:453px;width:136px;height:147px;background:#fff;border-radius:8px}
.sec-item{left:47px;width:122px;height:23px;background:var(--soft);display:flex;align-items:center;gap:6px;padding-left:6px;font-family:"Farro",sans-serif;font-size:4.5px;font-weight:500}
.sec-item.on{background:var(--blue);color:#fff;width:134px;clip-path:polygon(0 0,126px 0,100% 50%,126px 100%,0 100%)}
.sec-card{left:185px;top:453px;width:134px;height:146px;border-radius:8px;overflow:hidden;
  background:linear-gradient(180deg,#c99a63 0%,#6a5a55 45%,#1f2838 75%,#0c1220 100%)}

.stat-box{top:684px;height:79px;background:#fff;border:.6px solid #e2e2e2;text-align:center}
.stat-box h3{font-family:"Farro",sans-serif;font-weight:700;font-size:5px;color:var(--blue);margin-top:40px}
.stat-box p{font-size:3.6px;line-height:5.6px;color:var(--muted);margin:4px auto 0;width:64px}

.footer{left:0;top:785px;width:360px;height:126px;background:var(--navy);color:#fff}
.f-head{top:24px;font-family:"Farro",sans-serif;font-weight:500;font-size:4.8px}
.f-head::after{content:"";display:block;width:12px;height:1px;background:var(--gold);margin-top:2px}
.f-link{font-size:3.8px;color:#c9d2e3}

.note-h{left:424px;font-family:"Farro",sans-serif;font-weight:700;font-size:10px}
.note-p{left:424px;width:178px;font-size:6.5px;line-height:11.6px;color:#222;font-family:"Farro",sans-serif}
.thanks{left:30px;top:1162px;font-family:"Farro",sans-serif;font-weight:700;font-size:34px;color:#b7b7b7;white-space:nowrap}
</style>
</head>
<body>

<section class="board-head" role="img" aria-label="Dim city skyline at dusk"></section>
<div class="abs brand-mark"></div>
<div class="abs brand-name">Tarvenly Work Agency Ltd.</div>
<div class="abs brand-tag">The right people to power your business</div>
<h1 class="abs title">Website redesign for<br>job agency recruitment</h1>
<div class="abs meta" style="left:340px;top:102px">Font : Farro , Inter</div>
<div class="abs meta" style="left:340px;top:130px">Color :</div>
<div class="abs swatch" style="left:393px;background:var(--gold)"></div>
<div class="abs swatch" style="left:421px;background:var(--blue)"></div>
<div class="abs swatch" style="left:451px;background:#000"></div>

<div class="abs view-label">Desktop View</div>

<main class="site">
  <div class="abs site-logo"><div class="dot"></div><span>Tarvenly Work Agency Ltd.</span></div>
  <div class="abs topbar-call">
    <svg width="5" height="5" viewBox="0 0 10 10"><path d="M2 1l2 2-1 1.5a6 6 0 0 0 2.5 2.5L7 6l2 2-1.5 1.5C4 9 1 6 .5 2.5z" fill="#fff"/></svg>
    Toll Free: 1-888-555-0142
  </div>
  <div class="abs topbar-reg">Client Registration
    <svg width="8" height="4" viewBox="0 0 16 8"><path d="M0 4h14M10 1l4 3-4 3" stroke="#111" fill="none"/></svg>
  </div>
  <nav>
    <span class="abs nav active" style="left:134px">Home</span>
    <span class="abs nav" style="left:161px">Services</span>
    <span class="abs nav" style="left:192px">Candidates</span>
    <span class="abs nav" style="left:229px">Employers</span>
    <span class="abs nav" style="left:265px">About Us</span>
    <span class="abs nav" style="left:297px">Contact Us</span>
  </nav>

  <section class="abs hero" role="img" aria-label="Night city skyline in deep blue"></section>
  <h1 class="abs hero farro" style="left:39px;top:76px;width:170px;font-weight:700;font-size:12.6px;line-height:18px;color:#fff;background:none;height:auto">Connecting Canada’s Best Talent with its Most Essential Industries</h1>
  <p class="abs" style="left:39px;top:135px;width:130px;font-size:5px;line-height:8.2px;color:#e8ecf5">From specialized trades to executive leadership, we provide the precision staffing solutions that power national growth.</p>
  <div class="abs btn btn-blue" style="left:39px;top:165px;width:61px">For Candidates</div>
  <div class="abs btn btn-gold" style="left:107px;top:165px;width:61px">For Employers</div>
  <svg class="abs" style="left:172px;top:168px" width="30" height="12" viewBox="0 0 30 12"><path d="M1 2c2 8 14 10 26 3" stroke="#fff" stroke-width=".6" fill="none"/><path d="M24 3l3 2-3 2" stroke="#fff" stroke-width=".6" fill="none"/></svg>
  <span class="abs" style="left:176px;top:185px;font-size:4.2px;color:#fff">Our Services</span>

  <div class="abs orb" role="img" aria-label="Building under construction with cranes at sunset"></div>
  <div class="abs pin" style="left:206px;top:79px"><svg width="11" height="11" viewBox="0 0 12 12"><rect x="1" y="4" width="10" height="7" fill="none" stroke="#111" stroke-width=".8"/><path d="M3 4V1h3v3" fill="none" stroke="#111" stroke-width=".8"/></svg></div>
  <div class="abs pin" style="left:315px;top:80px"><svg width="11" height="11" viewBox="0 0 12 12"><rect x="1" y="3.5" width="10" height="7" rx="1" fill="none" stroke="#111" stroke-width=".8"/><path d="M4 3.5V2h4v1.5M1 6.5h10" fill="none" stroke="#111" stroke-width=".8"/></svg></div>
  <div class="abs pin on" style="left:198px;top:136px"><svg width="11" height="11" viewBox="0 0 12 12"><path d="M2 11V2h4v9M6 5h4v6M1 11h10" fill="none" stroke="#111" stroke-width=".8"/></svg></div>
  <div class="abs pin" style="left:322px;top:136px"><svg width="11" height="11" viewBox="0 0 12 12"><rect x="1" y="5" width="6" height="4" fill="none" stroke="#111" stroke-width=".8"/><path d="M7 7h3V3M10 9h1" stroke="#111" stroke-width=".8" fill="none"/><circle cx="3" cy="10" r="1" fill="#111"/><circle cx="8" cy="10" r="1" fill="#111"/></svg></div>
  <div class="abs pin" style="left:262px;top:180px"><svg width="11" height="11" viewBox="0 0 12 12"><path d="M1 11h10M3 11V6h6v5M6 6V1M4 3h4" fill="none" stroke="#111" stroke-width=".8"/></svg></div>
  <div class="abs service-pill">Construction and Trades <i></i></div>

  <div class="abs photo-frame"></div>
  <div class="abs photo-team" role="img" aria-label="Team meeting around an office table"></div>
  <div class="abs photo-hand" role="img" aria-label="Two professionals shaking hands"></div>
  <h2 class="abs sec-title" style="left:198px;top:249px;line-height:14px">Strengthening Your Business<br>with <span class="hl">Precision Staffing</span></h2>
  <p class="abs body-txt" style="left:199px;top:280px;width:128px">Tarvenly Work Agency Ltd. provides a complete range of recruitment services designed to keep pace with the rapidly changing demands of modern business. We are a Canada-wide team of search specialists and business consultants who thrive on delivering customized solutions that evolve with your market.</p>
  <p class="abs body-txt" style="left:199px;top:333px;width:128px">With specialist divisions immersed in the heartbeat of five core industries, we are the 'go-to' partners who successfully manage thousands of relationships every day. Our goal is simple: to provide results that are on-time, on-budget, and powered by the right people.”</p>
  <div class="abs btn btn-gold" style="left:199px;top:363px;width:61px;height:13px;font-size:4.5px;clip-path:polygon(0 0,100% 0,calc(100% - 4px) 100%,0 100%)">ABOUT AGENCY</div>

  <section class="abs sectors"></section>
  <h2 class="abs sec-title" style="left:0;width:360px;text-align:center;top:412px">Sectors We <span class="hl">Serve</span></h2>
  <p class="abs body-txt" style="left:75px;top:430px;width:210px;text-align:center">At Tarvenly Work Agency Ltd., we specialize in connecting high-caliber talent with industry-leading organizations. Our deep-rooted expertise across five core sectors allows us to provide tailored recruitment solutions that drive operational success and long-term growth</p>
  <div class="abs sec-list"></div>
  <div class="abs sec-item" style="top:461px"><svg width="12" height="12" viewBox="0 0 12 12"><path d="M1 11h10M3 11V6h6v5M6 6V1M4 3h4" fill="none" stroke="#111" stroke-width=".7"/></svg>OIL, GAS &amp; MINING</div>
  <div class="abs sec-item on" style="top:487px"><svg width="12" height="12" viewBox="0 0 12 12"><path d="M2 11V2h4v9M6 5h4v6M1 11h10" fill="none" stroke="#fff" stroke-width=".7"/></svg>CONSTRUCTION &amp; TRADES</div>
  <div class="abs sec-item" style="top:514px"><svg width="12" height="12" viewBox="0 0 12 12"><rect x="2" y="2" width="8" height="4" fill="none" stroke="#111" stroke-width=".7"/><rect x="1" y="6" width="10" height="5" fill="none" stroke="#111" stroke-width=".7"/></svg>WAREHOUSE &amp; LOGISTICS</div>
  <div class="abs sec-item" style="top:540px"><svg width="12" height="12" viewBox="0 0 12 12"><rect x="1" y="3.5" width="10" height="7" rx="1" fill="none" stroke="#111" stroke-width=".7"/><path d="M4 3.5V2h4v1.5M1 6.5h10" fill="none" stroke="#111" stroke-width=".7"/></svg>ADMINISTRATIVE</div>
  <div class="abs sec-item" style="top:566px"><svg width="12" height="12" viewBox="0 0 12 12"><path d="M1 11V5l3 2V5l3 2V2h3v9z" fill="none" stroke="#111" stroke-width=".7"/></svg>MANUFACTURING</div>
  <div class="abs sec-card" role="img" aria-label="High-rise construction site with tower cranes"></div>
  <div class="abs" style="left:195px;top:550px;height:10px;padding:0 3px;background:var(--gold);font-family:'Farro',sans-serif;font-weight:500;font-size:5px;line-height:10px">CONSTRUCTION &amp; TRADES</div>
  <div class="abs" style="left:266px;top:550px;width:11px;height:10px;background:var(--gold);clip-path:polygon(0 0,100% 0,80% 100%,0 100%)"><svg width="10" height="10" viewBox="0 0 10 10"><path d="M3 7l4-4M4 3h3v3" stroke="#111" stroke-width=".7" fill="none"/></svg></div>
  <p class="abs" style="left:195px;top:564px;width:118px;font-size:3.9px;line-height:7px;color:#fff">Tarvenly Work Agency is a premiere construction staffing agency that can provide you with reliable, experienced, and skilled tradespeople for projects all over Canada. We provide labour for temp, temp-to-hire, and permanent positions.</p>

  <h2 class="abs sec-title" style="left:0;width:360px;text-align:center;top:639px">YOUR VISION. OUR EXPERTISE. <span class="hl">REAL RESULTS</span></h2>
  <p class="abs body-txt" style="left:95px;top:656px;width:170px;text-align:center">At Tarvenly Work Agency Ltd., we strive to have a meaningful impact on every business we power. For years, we have helped clients and candidates find innovative staffing solutions through strategic partnership and knowledge sharing</p>
  <div class="abs stat-box" style="left:41px;width:91px"><h3>98 % CLIENT SATISFACTION</h3><p>Our clients report that Tarvenly provides the talent and data needed to complete their strategic priorities</p></div>
  <div class="abs stat-box" style="left:132px;width:96px;border-bottom:1.5px solid var(--gold)"><h3>#1 SPECIALIZED STAFFING</h3><p>Recognized as a leading brand in specialized recruitment for Western Canada's core industrial sectors</p></div>
  <div class="abs stat-box" style="left:228px;width:93px"><h3>10+ YEARS OF EXPERTISE</h3><p>Providing a complete range of recruitment services immersed in the heartbeat of Canada's core industries</p></div>
  <svg class="abs" style="left:71px;top:695px" width="26" height="22" viewBox="0 0 26 22"><g fill="none" stroke="#f2b90f" stroke-width=".8"><path d="M5 1l1 2 2 .3-1.5 1.4.4 2L5 5.8 3.1 6.7l.4-2L2 3.3 4 3z"/><path d="M13 0l1 2 2 .3-1.5 1.4.4 2L13 4.8l-1.9.9.4-2L10 2.3 12 2z"/><path d="M21 1l1 2 2 .3-1.5 1.4.4 2L21 5.8l-1.9.9.4-2L18 3.3 20 3z"/><circle cx="13" cy="12" r="2.5"/><path d="M8 21c0-4 10-4 10 0M2 21c0-3 7-3 7-1M17 20c0-2 7-2 7 1"/><circle cx="6" cy="14" r="2"/><circle cx="20" cy="14" r="2"/></g></svg>
  <svg class="abs" style="left:168px;top:694px" width="24" height="24" viewBox="0 0 24 24"><g fill="none" stroke="#f2b90f" stroke-width=".9"><circle cx="12" cy="9" r="7.5"/><path d="M12 5l1.2 2.4 2.6.4-1.9 1.8.5 2.6L12 11l-2.4 1.2.5-2.6-1.9-1.8 2.6-.4z"/><path d="M7 15l-3 7 3-1 1 3 3-7M17 15l3 7-3-1-1 3-3-7"/></g></svg>
  <svg class="abs" style="left:263px;top:694px" width="24" height="24" viewBox="0 0 24 24"><g fill="none" stroke="#f2b90f" stroke-width=".9"><path d="M3 22a9 9 0 0 1 18 0"/><path d="M7 22a5 5 0 0 1 10 0"/><path d="M12 22l3-5"/><path d="M8 1l.8 1.6 1.7.2-1.2 1.2.3 1.7L8 4.9l-1.6.8.3-1.7L5.5 2.8l1.7-.2zM16 1l.8 1.6 1.7.2-1.2 1.2.3 1.7L16 4.9l-1.6.8.3-1.7-1.2-1.2 1.7-.2z"/></g></svg>

  <footer class="abs footer" role="contentinfo">
    <div class="abs" style="left:40px;top:19px;width:22px;height:22px;border-radius:50%;border:1.5px solid #fff"></div>
    <div class="abs farro" style="left:39px;top:44px;font-size:4.3px;font-weight:500">Tarvenly Work Agency Ltd.</div>
    <div class="abs" style="left:39px;top:51px;font-size:2.6px;color:#c9d2e3">The right people to power your business</div>
    <div class="abs" style="left:50px;top:63px;width:8px;height:8px;border-radius:50%;border:.6px solid #fff"></div>
    <div class="abs" style="left:62px;top:63px;width:8px;height:8px;border-radius:50%;border:.6px solid #fff"></div>

    <div class="abs f-head" style="left:123px">Quick Links</div>
    <span class="abs f-link" style="left:124px;top:39px">Home</span>
    <span class="abs f-link" style="left:124px;top:49px">Services</span>
    <span class="abs f-link" style="left:124px;top:58px">Candidates</span>
    <span class="abs f-link" style="left:124px;top:68px">Employers</span>
    <span class="abs f-link" style="left:124px;top:77px">About us</span>
    <span class="abs f-link" style="left:124px;top:87px">Contact us</span>

    <div class="abs f-head" style="left:184px">Our Services</div>
    <span class="abs f-link" style="left:184px;top:39px">Oil, Gas and Mining</span>
    <span class="abs f-link" style="left:184px;top:49px">Administrative</span>
    <span class="abs f-link" style="left:184px;top:58px">Construction and Trades</span>
    <span class="abs f-link" style="left:184px;top:68px">Warehouse and Logistics</span>
    <span class="abs f-link" style="left:184px;top:77px">Manufacturing.</span>

    <div class="abs f-head" style="left:256px">Our Address</div>
    <svg class="abs" style="left:254px;top:38px" width="7" height="7" viewBox="0 0 10 10"><path d="M1 9h8M2 9V1h6v8M4 3h2M4 5h2" stroke="#c9d2e3" stroke-width=".7" fill="none"/></svg>
    <span class="abs f-link" style="left:266px;top:39px;width:60px;line-height:7px">410 Marrow St SW Calgary, AB, T2P 0X0</span>
    <svg class="abs" style="left:255px;top:58px" width="6" height="6" viewBox="0 0 10 10"><path d="M2 1l2 2-1 1.5a6 6 0 0 0 2.5 2.5L7 6l2 2-1.5 1.5C4 9 1 6 .5 2.5z" stroke="#c9d2e3" stroke-width=".7" fill="none"/></svg>
    <span class="abs f-link" style="left:266px;top:58px">Toll-Free: 1-888-555-0142</span>
    <svg class="abs" style="left:255px;top:70px" width="6" height="6" viewBox="0 0 10 10"><path d="M2 1l2 2-1 1.5a6 6 0 0 0 2.5 2.5L7 6l2 2-1.5 1.5C4 9 1 6 .5 2.5z" stroke="#c9d2e3" stroke-width=".7" fill="none"/></svg>
    <span class="abs f-link" style="left:266px;top:70px">403-555-0178</span>

    <span class="abs f-link" style="left:0;width:360px;text-align:center;top:113px">© Tarvenly Work Agency Ltd. | All rights reserved 2026</span>
  </footer>
</main>

<svg class="abs" style="left:366px;top:340px" width="64" height="22" viewBox="0 0 64 22"><path d="M0 2c25 0 45 6 58 16" stroke="#fff" stroke-width=".8" stroke-dasharray="2 2" fill="none"/><path d="M54 17l6 3-2-6z" fill="#fff"/></svg>
<h3 class="abs note-h" style="top:364px">How it works</h3>
<p class="abs note-p" style="top:380px">We'll list the service features in the hero section. When a user hovers over or clicks on an icon, the corresponding service image will be displayed in a round shape, along with the service name. I'll also add an option to redirect to the service detail page</p>

<svg class="abs" style="left:366px;top:739px" width="64" height="22" viewBox="0 0 64 22"><path d="M0 2c25 0 45 6 58 16" stroke="#222" stroke-width=".8" stroke-dasharray="2 2" fill="none"/><path d="M54 17l6 3-2-6z" fill="#222"/></svg>
<h3 class="abs note-h" style="top:764px">How it works</h3>
<p class="abs note-p" style="top:779px">We've got a plan to showcase our services. On the left, we'll list the service names. When you hover over a service, we'll display a relevant image on the right, along with a brief description and a link to learn more about that service</p>

<div class="abs thanks">Thank you for watching my works.</div>
</body>
</html>
```